Corvane Holdings , new business card design

investment firm with corporate clients . need double sided business card , vertical and horizontal options ,logo must be clear. prefer pantone colors only and sharp design. website also www.corvane.ae

Khalid Bin Tarrafi
Managing Director
Tel. +971 4 387 2940
Mobile +971 50 518 2403
khalid@corvane.ae
Q-Span Plaza, officw 18-B07, Warqa Gardens, Dubai

Contact Information for Business Card

Khalid Bin Tarrafi
Managing Director

Font styles to use
Serif

Colors

Designer to choose colors to be used in the design.

```html
<!DOCTYPE html>
<html lang="en">
<head>
<meta charset="utf-8">
<title>Corvane Holdings — Business Card</title>
<link rel="stylesheet" href="https://fonts.googleapis.com/css2?family=Jost:wght@400;500&display=swap">
<style>
  :root {
    --backdrop: #161616;
    --card: #232323;
    --card-edge: #2c2c2c;
    --ink: #f2f2f2;
    --accent: #4a7fb5;
  }
  * { margin: 0; padding: 0; box-sizing: border-box; }
  html, body {
    width: 1200px; height: 900px; overflow: hidden;
    background: var(--backdrop);
    font-family: "Jost", sans-serif;
    color: var(--ink);
  }
  .stage {
    position: relative; width: 1200px; height: 900px;
    display: flex; flex-direction: column; align-items: center; justify-content: center; gap: 40px;
  }
  .card {
    position: relative; width: 700px; height: 400px; overflow: hidden;
    background: linear-gradient(135deg, var(--card) 0%, #262626 60%, var(--card-edge) 100%);
    box-shadow: 0 16px 40px rgba(0,0,0,0.55);
  }
  .brand {
    display: flex; align-items: center;
    font-weight: 400; color: var(--ink);
    text-transform: uppercase; white-space: nowrap;
  }
  .brand-square { background: var(--accent); flex: none; }
  .card-front .brand {
    position: absolute; left: 50%; top: 50%; transform: translate(-50%, -50%);
    font-size: 34px; letter-spacing: 0.22em; gap: 14px;
  }
  .card-front .brand-square { width: 14px; height: 14px; }
  .card-back .brand {
    position: absolute; left: 40px; top: 150px; width: 300px; height: 30px;
    font-size: 20px; letter-spacing: 0.16em; gap: 12px;
  }
  .card-back .brand-square { width: 12px; height: 12px; }
  .divider {
    position: absolute; left: 362px; top: 110px; width: 2px; height: 190px;
    background: var(--accent);
  }
  .contact { position: absolute; left: 390px; top: 112px; width: 290px; }
  .contact-name {
    color: var(--accent); font-size: 20px; text-transform: uppercase; letter-spacing: 0.04em; line-height: 1.1;
  }
  .contact-role { font-size: 18px; margin-top: 2px; }
  .contact-address { font-size: 17px; line-height: 1.35; margin-top: 18px; }
  .contact-lines { list-style: none; margin-top: 12px; font-size: 18px; line-height: 1.4; }
  .contact-lines li { display: flex; align-items: center; gap: 12px; }
  .contact-lines svg { width: 12px; height: 12px; flex: none; }
</style>
</head>
<body>
<main class="stage">
  <section class="card card-front" aria-label="Card front">
    <div class="brand"><span class="brand-square"></span>Corvane Holdings</div>
  </section>

  <section class="card card-back" aria-label="Card back">
    <div class="brand"><span class="brand-square"></span>Corvane Holdings</div>
    <div class="divider"></div>
    <div class="contact">
      <p class="contact-name">Khalid Bin Tarrafi</p>
      <p class="contact-role">Managing Director</p>
      <p class="contact-address">Q-Span Plaza, officw 18-B07,<br>Warqa Gardens, Dubai</p>
      <ul class="contact-lines">
        <li>
          <svg viewBox="0 0 12 12" aria-hidden="true"><path d="M3 1 L5 3.5 L4 5 Q5 7 7 8 L8.5 7 L11 9 L9.5 11 Q5 11 1 6 Q1 3 3 1 Z" fill="none" stroke="#4a7fb5" stroke-width="1.2"/></svg>
          +971 4 387 2940
        </li>
        <li>
          <svg viewBox="0 0 12 12" aria-hidden="true"><rect x="3" y="0.8" width="6" height="10.4" rx="1" fill="none" stroke="#4a7fb5" stroke-width="1.2"/><line x1="5" y1="9.3" x2="7" y2="9.3" stroke="#4a7fb5" stroke-width="1"/></svg>
          +971 50 518 2403
        </li>
        <li>
          <svg viewBox="0 0 12 12" aria-hidden="true"><rect x="0.8" y="2.5" width="10.4" height="7" fill="none" stroke="#4a7fb5" stroke-width="1.2"/><path d="M1 3 L6 7 L11 3" fill="none" stroke="#4a7fb5" stroke-width="1.2"/></svg>
          khalid@corvane.ae
        </li>
      </ul>
    </div>
  </section>
</main>
</body>
</html>
```